Local Flower Farm Needs Business Card Design

I need business cards designed for a flower farm based in Eudora, Kansas.
Business Info:
We are a local cut flower farm located in Eudora, Kansas, founded by Corinne Haldwick. What started as a passion for agriculture and search for more joy in daily life has blossomed into a small business dedicated to providing the community with beautiful, fresh, and sustainable flowers. We specialize in local, seasonal blooms, ensuring that every petal reflects the care and dedication we pour into our craft. Our mission is to deliver the highest quality flowers directly to our customers through local farmers markets and to florists who share our commitment to sustainability. Join us in celebrating the beauty of nature, one bloom at a time!
Contact Details:
Corinne Haldwick
Owner
Phone 913-555-0147
Facebook: Rosalind Thorpe Gardens
Instagram: @RosalindThorpeGardens
Website: RosalindThorpeGardens.example
Target Market(s)
Wholesale to Florists and Direct to Consumer via Farmers Market
Industry/Entity Type
Florist, Farm
Contact Information for Business Card
Name, Contact Info, Logo
Look and feel
Each slider illustrates characteristics of the customer's brand and the style your logo design should communicate.

```html
<!DOCTYPE html>
<html lang="en">
<head>
<meta charset="utf-8">
<title>Rosalind Thorpe Gardens – Business Card</title>
<link href="https://fonts.googleapis.com/css2?family=Montserrat:wght@400;500;700&display=swap" rel="stylesheet">
<style>
  :root {
    --stage: #9a9a9a;
    --paper: #ffffff;
    --ink: #0a262c;
    --ink-text: #111a1c;
    --teal-glow: #5bc8e8;
  }
  * { margin: 0; padding: 0; box-sizing: border-box; }
  html, body {
    width: 1093px; height: 1200px; overflow: hidden;
    background: var(--stage);
    font-family: "Montserrat", sans-serif;
  }
  .canvas { position: relative; width: 1093px; height: 1200px; }

  .card {
    position: absolute; left: 264px; width: 597px; height: 364px;
    overflow: hidden;
  }
  .card--front { top: 224px; background: var(--paper); }
  .card--back  { top: 615px; height: 368px; background: var(--ink); }

  .holder { position: absolute; left: 26px; top: 44px; }
  .holder__name {
    font-weight: 700; font-size: 24px; color: var(--ink); letter-spacing: 0.2px;
  }
  .holder__role { font-size: 14px; color: var(--ink-text); margin-top: 1px; }

  .contacts { position: absolute; left: 26px; top: 252px; list-style: none; }
  .contacts__item {
    display: flex; align-items: center; height: 22px;
    font-size: 14px; color: var(--ink-text);
  }
  .contacts__icon { width: 14px; height: 14px; margin-right: 7px; flex: none; }

  .brand-band {
    position: absolute; left: 333px; top: 0; width: 211px; height: 100%;
    background: var(--ink);
  }
  .brand-seal {
    position: absolute; left: 326px; top: 90px; width: 226px; height: 226px;
    border-radius: 50%; background: var(--paper);
    display: flex; align-items: center; justify-content: center; text-align: center;
  }
  .brand-seal__name {
    font-weight: 700; font-size: 20px; line-height: 1.3; color: var(--ink);
    width: 170px;
  }

  .back-pattern {
    position: absolute; inset: 0;
    background: linear-gradient(135deg, var(--teal-glow) 0%, #2d6f80 22%, var(--ink) 55%, var(--ink) 100%);
    opacity: 0.85;
  }
  .back-mark {
    position: absolute; left: 332px; top: 224px; width: 200px; text-align: center;
    font-weight: 700; font-size: 16px; line-height: 1.25; color: var(--paper);
  }
</style>
</head>
<body>
<main class="canvas">

  <section class="card card--front" aria-label="Business card front">
    <div class="holder">
      <h1 class="holder__name">Corinne Haldwick</h1>
      <p class="holder__role">Owner</p>
    </div>

    <ul class="contacts">
      <li class="contacts__item">
        <svg class="contacts__icon" viewBox="0 0 24 24" aria-hidden="true">
          <path fill="var(--ink-text)" d="M6.6 10.8a15.1 15.1 0 0 0 6.6 6.6l2.2-2.2c.3-.3.7-.4 1-.2 1.1.4 2.3.6 3.6.6.6 0 1 .4 1 1V20c0 .6-.4 1-1 1A17 17 0 0 1 3 4c0-.6.4-1 1-1h3.5c.6 0 1 .4 1 1 0 1.3.2 2.5.6 3.6.1.3 0 .7-.2 1z"/>
        </svg>913-555-0147</li>
      <li class="contacts__item">
        <svg class="contacts__icon" viewBox="0 0 24 24" aria-hidden="true"><circle cx="12" cy="12" r="11" fill="var(--ink-text)"/></svg>Rosalind Thorpe Gardens</li>
      <li class="contacts__item">
        <svg class="contacts__icon" viewBox="0 0 24 24" aria-hidden="true"><circle cx="12" cy="12" r="11" fill="var(--ink-text)"/></svg>@RosalindThorpeGardens</li>
      <li class="contacts__item">
        <svg class="contacts__icon" viewBox="0 0 24 24" aria-hidden="true">
          <circle cx="12" cy="12" r="10" fill="none" stroke="var(--ink-text)" stroke-width="2"/>
          <ellipse cx="12" cy="12" rx="4.5" ry="10" fill="none" stroke="var(--ink-text)" stroke-width="1.8"/>
          <line x1="2" y1="12" x2="22" y2="12" stroke="var(--ink-text)" stroke-width="1.8"/>
        </svg>www.RosalindThorpeGardens.example</li>
    </ul>

    <div class="brand-band"></div>
    <div class="brand-seal">
      <p class="brand-seal__name">Rosalind Thorpe Gardens</p>
    </div>
  </section>

  <section class="card card--back" aria-label="Business card back">
    <div class="back-pattern" role="img" aria-label="Repeating brand monogram pattern fading from bright teal to deep teal"></div>
    <p class="back-mark">Rosalind Thorpe Gardens</p>
  </section>

</main>
</body>
</html>
```